Promotional business a5 Notepad design

I am looking for a custom a5 notepad design as a promotional item to give away to customers etc.
Attached will be a desk planner we had designed feel free to use as a reference.
We want the notepad to have lines running horizontal not squares like the desk planner example.

Industry/Entity Type

Hydraulic / industrial

Colors

Designer to choose colors to be used in the design.

```html
<!DOCTYPE html>
<html lang="en">
<head>
<meta charset="utf-8">
<title>Meridian Hose and Couplings – A5 Notepad</title>
<link rel="stylesheet" href="https://fonts.googleapis.com/css2?family=Inter:wght@400;500;800&display=swap">
<style>
  :root {
    --backdrop: #dcdde0;
    --paper: #f1f2f4;
    --brand-blue: #1230c0;
    --ink-black: #141414;
    --rule-grey: #8c8c8e;
    --steel: #9aa3ad;
    --white: #ffffff;
  }
  * { box-sizing: border-box; margin: 0; padding: 0; }
  html, body {
    width: 1200px; height: 1141px; overflow: hidden;
    background: var(--backdrop);
    font-family: "Inter", sans-serif;
  }
  .notepad-page {
    position: absolute; left: 208px; top: 20px;
    width: 783px; height: 1100px;
    background: var(--paper);
    box-shadow: 0 2px 8px rgba(0,0,0,0.12);
  }
  .brand-header {
    position: absolute; top: 72px; left: 0; right: 0;
    display: flex; justify-content: center; align-items: center; gap: 10px;
  }
  .brand-dot {
    width: 34px; height: 34px; border-radius: 50%;
    background: var(--ink-black);
  }
  .brand-name {
    font-weight: 800; font-size: 24px; letter-spacing: 0.5px;
    color: var(--brand-blue); text-transform: uppercase;
  }
  .writing-lines {
    position: absolute; left: 56px; width: 670px; top: 179px;
    list-style: none;
  }
  .writing-lines li {
    height: 46.4px; border-top: 1.2px solid var(--rule-grey);
  }
  .writing-lines li:last-child { height: 0; }
  .footer-stripe {
    position: absolute; left: 0; right: 0; height: 5px;
  }
  .footer-stripe.top {
    top: 1032px;
    background: linear-gradient(90deg, var(--ink-black) 0%, var(--ink-black) 40%, transparent 40%, transparent 40.8%, #6d7580 41%, #d0d4d9 70%, #7c848e 100%);
  }
  .footer-stripe.bottom {
    top: 1067px;
    background: linear-gradient(90deg, #5b626b 0%, #d9dde1 35%, #6e7680 60%, transparent 60.2%, transparent 60.8%, var(--ink-black) 61%, var(--ink-black) 100%);
  }
  .contact-band {
    position: absolute; left: 0; right: 0; top: 1040px; height: 24px;
    background: var(--brand-blue);
    display: flex; justify-content: center; align-items: center; gap: 5px;
    color: var(--white); font-size: 11.4px; font-weight: 400; white-space: nowrap;
  }
  .contact-item { display: inline-flex; align-items: center; gap: 3px; }
  .contact-item svg { width: 9px; height: 9px; fill: var(--white); }
</style>
</head>
<body>
  <main class="notepad-page">
    <header class="brand-header">
      <span class="brand-dot"></span>
      <span class="brand-name">Meridian Hose and Couplings</span>
    </header>

    <ul class="writing-lines">
      <li></li><li></li><li></li><li></li><li></li><li></li>
      <li></li><li></li><li></li><li></li><li></li><li></li>
      <li></li><li></li><li></li><li></li><li></li><li></li>
    </ul>

    <div class="footer-stripe top"></div>
    <footer class="contact-band">
      <span class="contact-item">
        <svg viewBox="0 0 10 10"><path d="M5 0a3.5 3.5 0 0 0-3.5 3.5C1.5 6 5 10 5 10s3.5-4 3.5-6.5A3.5 3.5 0 0 0 5 0zm0 5a1.4 1.4 0 1 1 0-2.8A1.4 1.4 0 0 1 5 5z"/></svg>
        Servicing the Greater Riverton area
      </span>
      <span class="contact-item">
        <svg viewBox="0 0 10 10"><path d="M2 0.5l1.6 2.2-0.9 1.1c0.6 1.3 1.6 2.3 2.9 2.9l1.1-0.9L9 7.4 8.3 9.3C4.2 9.3 0.7 5.8 0.7 1.7z"/></svg>
        0400 123 456
      </span>
      <span class="contact-item">
        <svg viewBox="0 0 10 10"><path d="M0 2h10v0.6L5 5.6 0 2.6zM0 3.6l5 3 5-3V8H0z"/></svg>
        hello@meridianhose.com.au
      </span>
      <span class="contact-item">
        <svg viewBox="0 0 10 10"><path d="M5 0a5 5 0 1 0 0 10A5 5 0 0 0 5 0zm0 1c.6 0 1.3 1.2 1.5 3h-3C3.7 2.2 4.4 1 5 1zM1.1 4h1.4a9 9 0 0 0 0 2H1.1a4 4 0 0 1 0-2zm2.4 2h3c-.2 1.8-.9 3-1.5 3S3.7 7.8 3.5 6zm4-2h1.4a4 4 0 0 1 0 2H7.5a9 9 0 0 0 0-2z"/></svg>
        meridianhose.com.au
      </span>
    </footer>
    <div class="footer-stripe bottom"></div>
  </main>
</body>
</html>
```